Business Card Design

IT Solutions company.

I need a professional looking design with my company logo if possible.

Logo is located here:
http://www.brunelwavesystems.co.uk/dev/images/logo1.jpg
Feel free to redesign the logo if you think you have any better suggestions.

Our services include, IT Infrastructure/Telephony Maintenance & Hosting Services. Linux and Windows Solutions, App Development.

Out website is currently under development:
http://www.brunelwavesystems.co.uk/dev/

I'm looking for a colourful but professional looking business card.

Industry/Entity Type

Business

Contact Information for Business Card

BW Brunel Wavesystems Ltd
Martin Hollisby
07700958312
www.brunelwavesystems.co.uk
mhollisby@brunelwavesystems.co.uk

```html
<!DOCTYPE html>
<html lang="en">
<head>
<meta charset="utf-8">
<title>Brunel Wavesystems – Business Card</title>
<link rel="stylesheet" href="https://fonts.googleapis.com/css2?family=Exo+2:wght@400;600;700&display=swap">
<style>
  :root {
    --bg: #d9dadb;
    --card: #ffffff;
    --card-edge: #e6e6e6;
    --brand-blue: #1a46b0;
    --ink: #2b2b2b;
    --ink-soft: #4a4a4a;
    --panel: #3a3a3a;
    --panel-rule: #8a8a8a;
    --on-panel: #ffffff;
  }
  * { box-sizing: border-box; margin: 0; padding: 0; }
  html, body {
    width: 1200px; height: 894px; overflow: hidden;
    background: var(--bg);
    font-family: "Exo 2", sans-serif;
  }
  .canvas {
    position: relative; width: 1200px; height: 894px;
  }
  .card {
    position: absolute; left: 290px;
    width: 620px; height: 354px;
    background: var(--card);
    border: 1px solid var(--card-edge);
    box-shadow: 0 6px 18px rgba(0,0,0,.12);
    overflow: hidden;
  }
  .card--back { top: 50px; }
  .card--front { top: 490px; }

  .accent-band {
    position: absolute; right: 0;
    background: var(--brand-blue);
  }
  .card--back .accent-band { top: 96px; width: 160px; height: 30px; }
  .card--front .accent-band { top: 92px; width: 170px; height: 26px; }

  .brand {
    position: absolute; display: flex; align-items: center;
    color: var(--ink); font-weight: 700;
  }
  .brand__mark {
    border: 6px solid var(--brand-blue); border-radius: 50%; flex: none;
  }
  .card--back .brand { left: 70px; top: 128px; gap: 22px; font-size: 36px; }
  .card--back .brand__mark { width: 96px; height: 96px; }
  .card--front .brand { left: 28px; top: 24px; gap: 12px; font-size: 16px; }
  .card--front .brand__mark { width: 50px; height: 50px; border-width: 4px; }

  .person {
    position: absolute; left: 270px; top: 124px;
  }
  .person__name {
    color: var(--brand-blue); font-weight: 600;
    font-size: 28px; letter-spacing: 2px; text-transform: uppercase; line-height: 1;
  }
  .person__title {
    color: var(--ink-soft); font-weight: 400;
    font-size: 17px; letter-spacing: 1.5px; text-transform: uppercase; margin-top: 6px;
  }

  .contact-panel {
    position: absolute; left: 18px; right: 18px; top: 196px; bottom: 16px;
    background: var(--panel); border-radius: 16px;
    display: grid; grid-template-columns: 1fr 1.3fr 1fr;
    color: var(--on-panel);
  }
  .contact-panel__cell {
    display: flex; flex-direction: column; align-items: center; justify-content: center;
    gap: 10px; padding: 0 10px; text-align: center;
    font-size: 12.5px; letter-spacing: .5px; line-height: 1.5;
  }
  .contact-panel__cell + .contact-panel__cell { border-left: 1px solid var(--panel-rule); }
  .contact-panel__icon { width: 28px; height: 28px; }
</style>
</head>
<body>
<main class="canvas">

  <section class="card card--back" aria-label="Business card, logo side">
    <div class="accent-band"></div>
    <div class="brand">
      <span class="brand__mark"></span>
      <span class="brand__name">BW Brunel Wavesystems Ltd</span>
    </div>
  </section>

  <section class="card card--front" aria-label="Business card, contact side">
    <div class="brand">
      <span class="brand__mark"></span>
      <span class="brand__name">BW Brunel Wavesystems Ltd</span>
    </div>
    <div class="accent-band"></div>
    <div class="person">
      <p class="person__name">Martin Hollisby</p>
      <p class="person__title">Creative Director</p>
    </div>

    <div class="contact-panel">
      <div class="contact-panel__cell contact-panel__cell--phone">
        <svg class="contact-panel__icon" viewBox="0 0 28 28" fill="none" stroke="currentColor" stroke-width="2" aria-hidden="true">
          <path d="M4 10c0-3 4-5 10-5s10 2 10 5l-3 2-3-2v-2H10v2l-3 2z" fill="currentColor"/>
          <rect x="6" y="14" width="16" height="9" rx="2"/>
          <circle cx="14" cy="18.5" r="2" fill="currentColor"/>
        </svg>
        <span>07700958312</span>
      </div>
      <div class="contact-panel__cell contact-panel__cell--web">
        <svg class="contact-panel__icon" viewBox="0 0 28 28" fill="none" stroke="currentColor" stroke-width="1.8" aria-hidden="true">
          <circle cx="14" cy="14" r="11"/>
          <ellipse cx="14" cy="14" rx="5" ry="11"/>
          <path d="M3 14h22M5 8h18M5 20h18"/>
        </svg>
        <span>mhollisby@brunelwavesystems.co.uk<br>www.brunelwavesystems.co.uk</span>
      </div>
      <div class="contact-panel__cell contact-panel__cell--address">
        <svg class="contact-panel__icon" viewBox="0 0 28 28" aria-hidden="true">
          <path d="M14 2a8 8 0 0 0-8 8c0 6 8 16 8 16s8-10 8-16a8 8 0 0 0-8-8z" fill="currentColor"/>
          <circle cx="14" cy="10" r="3" fill="var(--panel)"/>
        </svg>
        <span>Unit 4, Harbour Court<br>Bristol BS1</span>
      </div>
    </div>
  </section>

</main>
</body>
</html>
```